Business card design needed

I run a Beautician studio (for 7 years now)
I offer
- Velmo Body Sugaring
- Ruby Glaze
- Nails
- Facials
- Manicure
- Foot Treatment
It might not be necessary to list all those treatments?
Maybe the link to the Website is sufficient?
I leave that up to you ...
(more info on www.FernAndDewByLenka.com.au)
Velmo BodySugaring is our biggest success, It replaces waxing.
I would like to incorporate the logo into the Business Card.
We had many complaints regarding our old Business Cards as the Phone Number was to small.
On the backside, we would like a "your next Appointment" section.
Looking forward to you Design, cheers ... Lenka
Industry/Entity Type
Business
Contact Information for Business Card
Fern by Dew by Lenka
14 Korrin Sqr 3942 Dunmore
www.FernAndDewByLenka.com.au
03 9481 2267

```html
<!DOCTYPE html>
<html lang="en">
<head>
<meta charset="utf-8">
<title>Fern &amp; Dew by Lenka – Business Card</title>
<link rel="stylesheet" href="https://fonts.googleapis.com/css2?family=Ubuntu:ital,wght@0,400;0,500;1,500;1,700&family=Tinos&display=swap">
<style>
  :root {
    --backdrop: #e9e6e2;
    --card: #ffffff;
    --ink: #333333;
    --ink-soft: #555555;
    --rule: #8a8a8a;
    --band: #3e3e40;
    --band-line: #b5b5b5;
    --brand: #d9761f;
    --label: #1a1a1a;
  }
  * { box-sizing: border-box; margin: 0; padding: 0; }
  html, body { width: 1200px; height: 788px; overflow: hidden; }
  body {
    position: relative;
    background: var(--backdrop);
    font-family: "Ubuntu", sans-serif;
    color: var(--ink);
  }
  .side-label {
    position: absolute;
    font-size: 21px;
    color: var(--label);
    transform: translateX(-50%);
  }
  .card {
    position: absolute;
    width: 525px;
    height: 300px;
    background: var(--card);
    border-radius: 18px;
    overflow: hidden;
    box-shadow: 0 4px 10px rgba(0,0,0,0.25);
  }
  .card > * { position: absolute; }
  .brand-mark {
    display: flex;
    align-items: center;
    gap: 6px;
    font-size: 15px;
    font-weight: 500;
    color: var(--brand);
    letter-spacing: 1px;
    white-space: nowrap;
  }
  .brand-mark .dot {
    width: 12px; height: 12px; border-radius: 50%;
    background: var(--brand);
  }
  .centered { left: 0; right: 0; text-align: center; }

  /* Front */
  .card--front { left: 337px; top: 74px; }
  .card--front .brand-mark { top: 58px; left: 50%; transform: translateX(-50%); }
  .studio-name {
    top: 122px;
    font-size: 35px;
    font-weight: 400;
    letter-spacing: 1.5px;
    color: var(--ink);
  }
  .contact-line { font-size: 17px; color: var(--ink); }
  .contact-line b { font-style: italic; font-weight: 700; }
  .contact-line--phone { top: 197px; }
  .contact-line--web { top: 223px; }
  .front-band { left: 0; top: 0; width: 525px; height: 300px; }
  .address { top: 270px; font-size: 16px; color: #ffffff; }

  /* Back 1 */
  .card--back1 { left: 54px; top: 444px; }
  .card--back1 .studio-name { top: 12px; font-size: 25px; }
  .title-rule { left: 0; right: 0; top: 50px; height: 1px; background: var(--rule); }
  .col-heading { font-size: 18px; font-style: italic; font-weight: 700; color: var(--ink); }
  .offer-heading { left: 30px; top: 70px; }
  .offer-list {
    left: 30px; top: 97px;
    list-style: none;
    font-family: "Tinos", serif;
    font-size: 15px;
    line-height: 20px;
    color: var(--ink-soft);
  }
  .offer-list li::before {
    content: ""; display: inline-block;
    width: 4px; height: 4px; background: var(--ink-soft);
    margin-right: 7px; vertical-align: middle;
  }
  .col-divider { left: 207px; top: 72px; width: 2px; height: 140px; background: #777; }
  .appt-heading { left: 244px; top: 70px; }
  .appt-field { left: 244px; font-size: 16px; color: var(--ink); display: flex; align-items: flex-end; }
  .appt-field .blank { border-bottom: 1px solid var(--ink); height: 18px; margin-left: 2px; }
  .hours-heading { top: 238px; font-size: 14px; font-style: italic; font-weight: 700; }
  .hours-line { top: 261px; font-size: 13px; word-spacing: 1px; }

  /* Back 2 */
  .card--back2 { left: 621px; top: 444px; }
  .card--back2 .hours-title {
    left: 33px; top: 28px;
    font-size: 20px; font-style: italic; font-weight: 500; letter-spacing: 1.2px;
  }
  .hours-row { left: 30px; font-size: 18px; }
  .card--back2 .brand-mark { right: 30px; top: 90px; font-size: 13px; }
  .card--back2 .split-rule { left: 30px; right: 30px; top: 116px; height: 1px; background: #c8c8c8; }
  .appt-row { left: 0; right: 0; display: flex; justify-content: center; align-items: flex-end; font-size: 18px; gap: 4px; }
  .appt-row .blank { border-bottom: 1px solid var(--ink); height: 16px; display: inline-block; }
  .day-row { left: 0; right: 0; top: 248px; display: flex; justify-content: center; gap: 14px; font-size: 17px; }
  .day { display: flex; align-items: center; gap: 10px; }
  .day .box { width: 22px; height: 22px; border: 1px solid var(--ink); }
</style>
</head>
<body>

<span class="side-label" style="left:600px; top:34px;">Front</span>
<span class="side-label" style="left:323px; top:403px;">Back - 1</span>
<span class="side-label" style="left:897px; top:403px;">Back - 2</span>

<section class="card card--front">
  <div class="brand-mark"><span class="dot"></span>Velmo Body Sugaring</div>
  <h1 class="studio-name centered">FERN &amp; DEW BY LENKA</h1>
  <p class="contact-line contact-line--phone centered"><b>phone</b> 03 9481 2267</p>
  <p class="contact-line contact-line--web centered"><b>web</b> www.FernAndDewByLenka.com.au</p>
  <svg class="front-band" viewBox="0 0 525 300" aria-hidden="true">
    <path d="M0 268 Q 262 244 525 276" fill="none" stroke="var(--band-line)" stroke-width="3"/>
    <path d="M0 275 Q 262 251 525 282 L525 300 L0 300 Z" fill="var(--band)"/>
  </svg>
  <p class="address centered">14 Korrin Sqr, 3942 Dunmore</p>
</section>

<section class="card card--back1">
  <h2 class="studio-name centered">FERN &amp; DEW BY LENKA</h2>
  <div class="title-rule"></div>

  <h3 class="col-heading offer-heading">I offer</h3>
  <ul class="offer-list">
    <li>Velmo Body Sugaring</li>
    <li>Ruby Glaze</li>
    <li>Nails</li>
    <li>Facials</li>
    <li>Manicure</li>
    <li>Foot Treatment</li>
  </ul>

  <div class="col-divider"></div>

  <h3 class="col-heading appt-heading">An Appointment</h3>
  <p class="appt-field" style="top:112px;">Name<span class="blank" style="width:215px;"></span></p>
  <p class="appt-field" style="top:152px;">Date<span class="blank" style="width:223px;"></span></p>
  <p class="appt-field" style="top:191px;">time<span class="blank" style="width:158px;"></span>&nbsp;am / pm</p>

  <p class="hours-heading centered">Hours of Operation</p>
  <p class="hours-line centered">Mon. to Fri.&nbsp; 7.30am - 7.00pm&nbsp;&nbsp;&nbsp;&nbsp;&nbsp;&nbsp;&nbsp;&nbsp;&nbsp; Sat. 7.30am - 12.00pm</p>
</section>

<section class="card card--back2">
  <h2 class="hours-title">Hours of Operation</h2>
  <p class="hours-row" style="top:61px;">Monday to Friday -&nbsp; 7.30am - 7.00pm</p>
  <p class="hours-row" style="top:85px;">Saturday - 7.30am - 12.00pm</p>
  <div class="brand-mark"><span class="dot"></span>Velmo Body Sugaring</div>
  <div class="split-rule"></div>

  <p class="appt-row" style="top:144px;"><span class="blank" style="width:260px;"></span>&nbsp;has an appointment</p>
  <p class="appt-row" style="top:194px;">Date :<span class="blank" style="width:40px;"></span>&nbsp;/&nbsp;<span class="blank" style="width:42px;"></span>&nbsp;/&nbsp;<span class="blank" style="width:52px;"></span>&nbsp;&nbsp;@&nbsp;<span class="blank" style="width:40px;"></span>&nbsp;:&nbsp;<span class="blank" style="width:50px;"></span>am / pm</p>

  <div class="day-row">
    <span class="day"><span class="box"></span>Mon.</span>
    <span class="day"><span class="box"></span>Tue.</span>
    <span class="day"><span class="box"></span>Wed.</span>
    <span class="day"><span class="box"></span>Thu.</span>
    <span class="day"><span class="box"></span>Fri.</span>
  </div>
</section>

</body>
</html>
```